Business Card and Letterhead for Pimlu - modern real estate business

I need a double sided business card design for Pimlu. Please see business card brief here https://files.trelvonadocs.com/sheet/r/7QzTmWbaXLJnoPEd-kRyUgFhHsstbvCe2qfoMxDa_pz/view?mode=shared

Please feel free to design the business cards however you feel best. I am happy to give some creative freedoms and then provide feedback from there.

Please then also create a letterhead to match the business card design

Colors

Designer to choose colors to be used in the design.

Requirements
Must have
• Must be a modern, elegant business card which looks very professional

```html
<!DOCTYPE html>
<html lang="en">
<head>
<meta charset="utf-8">
<title>Pimlu Business Card</title>
<link href="https://fonts.googleapis.com/css2?family=Montserrat:wght@400;500;700;800&display=swap" rel="stylesheet">
<style>
  :root {
    --brand-red: #e30613;
    --ink: #1d1d1d;
    --charcoal: #2a2a2c;
    --paper: #ffffff;
    --backdrop: #ececec;
    --photo-light: #d9d9db;
    --photo-dark: #8a8a8e;
  }
  * { margin: 0; padding: 0; box-sizing: border-box; }
  html, body { width: 1200px; height: 800px; overflow: hidden; }
  body {
    background: var(--backdrop);
    font-family: "Montserrat", sans-serif;
    position: relative;
  }
  .card {
    position: absolute;
    top: 245px;
    width: 540px;
    height: 309px;
    overflow: hidden;
    box-shadow: 0 6px 18px rgba(0,0,0,0.18);
  }
  .card-front { left: 40px; background: var(--brand-red); }
  .card-back { left: 620px; background: var(--paper); }

  .front-wordmark {
    position: absolute;
    left: 0; right: 0; top: 112px;
    text-align: center;
    color: var(--paper);
    font-weight: 800;
    font-size: 72px;
    letter-spacing: 6px;
    line-height: 1;
  }

  .agent-photo {
    position: absolute;
    left: 0; top: 0;
    width: 240px; height: 266px;
    background: linear-gradient(160deg, var(--photo-light), var(--photo-dark));
  }
  .back-wordmark {
    position: absolute;
    right: 24px; top: 40px;
    color: var(--brand-red);
    font-weight: 800;
    font-size: 56px;
    letter-spacing: 4px;
    line-height: 1;
  }
  .agent-name {
    position: absolute;
    right: 24px; top: 118px;
    color: var(--brand-red);
    font-weight: 700;
    font-size: 20px;
    letter-spacing: 1.5px;
  }
  .agent-title {
    position: absolute;
    right: 24px; top: 146px;
    color: var(--ink);
    font-weight: 500;
    font-size: 14px;
  }
  .contact-rule {
    position: absolute;
    left: 240px; right: 0; top: 176px;
    height: 4px;
    background: var(--ink);
  }
  .contact-band {
    position: absolute;
    left: 240px; right: 0; top: 180px;
    height: 82px;
    background: var(--brand-red);
  }
  .contact-list {
    list-style: none;
    position: absolute;
    right: 24px; top: 190px;
    color: var(--paper);
    font-size: 14px;
    font-weight: 500;
  }
  .contact-item {
    display: flex;
    justify-content: flex-end;
    align-items: center;
    gap: 8px;
    height: 21px;
  }
  .contact-icon { width: 12px; height: 12px; fill: var(--paper); }
  .address-band {
    position: absolute;
    left: 0; right: 0; top: 266px; bottom: 0;
    background: var(--charcoal);
    color: var(--paper);
    font-size: 15px;
    font-weight: 500;
    padding: 12px 0 0 20px;
  }
</style>
</head>
<body>

<section class="card card-front" aria-label="Business card front">
  <div class="front-wordmark">PIMLU</div>
</section>

<section class="card card-back" aria-label="Business card back">
  <div class="agent-photo" role="img" aria-label="Portrait photo of the agent in a dark suit"></div>
  <div class="back-wordmark">PIMLU</div>
  <div class="agent-name">DANE CORVEL</div>
  <div class="agent-title">Licenced Real Estate Agent</div>
  <div class="contact-rule"></div>
  <div class="contact-band"></div>
  <ul class="contact-list">
    <li class="contact-item">0412 390 418
      <svg class="contact-icon" viewBox="0 0 24 24" aria-hidden="true"><path d="M6.6 10.8a15.1 15.1 0 0 0 6.6 6.6l2.2-2.2a1 1 0 0 1 1-.25 11.4 11.4 0 0 0 3.6.57 1 1 0 0 1 1 1V20a1 1 0 0 1-1 1A17 17 0 0 1 3 4a1 1 0 0 1 1-1h3.5a1 1 0 0 1 1 1c0 1.25.2 2.45.57 3.57a1 1 0 0 1-.25 1z"/></svg>
    </li>
    <li class="contact-item">dane@pimlu.com
      <svg class="contact-icon" viewBox="0 0 24 24" aria-hidden="true"><path d="M2 5h20v14H2z M4 7v.4l8 5 8-5V7l-8 5z" fill-rule="evenodd"/></svg>
    </li>
    <li class="contact-item">www.pimlu.com
      <svg class="contact-icon" viewBox="0 0 24 24" aria-hidden="true"><path d="M12 2a10 10 0 1 0 0 20 10 10 0 0 0 0-20zm6.9 6h-3a15 15 0 0 0-1.3-3.9A8 8 0 0 1 18.9 8zM12 4c.8 1.2 1.5 2.5 1.9 4h-3.8c.4-1.5 1.1-2.8 1.9-4zM4.3 14a8 8 0 0 1 0-4h3.4a16 16 0 0 0 0 4zm.8 2h3a15 15 0 0 0 1.3 3.9A8 8 0 0 1 5.1 16zm3-8h-3a8 8 0 0 1 4.3-3.9A15 15 0 0 0 8.1 8zM12 20c-.8-1.2-1.5-2.5-1.9-4h3.8c-.4 1.5-1.1 2.8-1.9 4zm2.3-6H9.7a14 14 0 0 1 0-4h4.6a14 14 0 0 1 0 4zm.3 5.9a15 15 0 0 0 1.3-3.9h3a8 8 0 0 1-4.3 3.9zm1.7-5.9a16 16 0 0 0 0-4h3.4a8 8 0 0 1 0 4z"/></svg>
    </li>
  </ul>
  <div class="address-band">PO Box 7316, Larrow Vale NSW 2790</div>
</section>

</body>
</html>
```